a business advisory consulting website

I need a website 3-5 pages to sell my professional services in IT and Project management Consulting. My company name is Crestline Advisory Consulting. I want it to be device friendly and easy to navigate for the busy executive however intriguing enough.
I have attached some info I drafted on About the company and personal Bio. Also there is a website that I really like that I have attached the initial site pdf and websites that I like are here: https://tollmeradvisors.example, https://quarvelanalytics.example, https://www.dorvikstudylearning.example as examples. Thanks
Updates

Hi Designers, I have uploaded the logo in 3D .png format, to assist in the web design.

Target Market(s)

B2B, governments, IT companies, Project Management companies and Consulting firms, small medium enterprises to large corporate enterprises.

Industry/Entity Type

It Professional

Coding

Coded - Design and coding required

Number of Pages Required

5+ page

Font styles to use
Sans Serif

Requirements
Must have
• Home, About company, the team, what we do and contact us
Nice to have
• Blog
Should not have
• pop ups, flash

```html
<!DOCTYPE html>
<html lang="en">
<head>
<meta charset="utf-8">
<title>Crestline Advisory Consulting</title>
<link href="https://fonts.googleapis.com/css2?family=Baloo+2:wght@700;800&family=Poppins:wght@300;400;500&display=swap" rel="stylesheet">
<style>
:root{
  --red:#e42528;
  --navy:#222846;
  --ink:#1f2440;
  --muted:#8e8e8e;
  --soft:#f9f9f9;
  --white:#ffffff;
}
*{margin:0;padding:0;box-sizing:border-box}
html,body{width:1200px;height:2258px;overflow:hidden}
body{position:relative;background:var(--white);font-family:"Poppins",sans-serif;color:var(--ink)}
.abs{position:absolute}

/* top contact bar */
.topbar{left:540px;top:0;width:499px;height:37px;background:var(--red);clip-path:polygon(0 0,100% 0,100% 100%,14px 100%)}
.topbar-item{top:12px;color:var(--white);font-size:11.5px;line-height:14px;display:flex;align-items:center;gap:8px;white-space:nowrap}
.topbar-social{top:0;width:37px;height:37px;border-left:1px solid rgba(255,255,255,.35);display:flex;align-items:center;justify-content:center}
.topbar-social span{width:10px;height:10px;border-radius:50%;background:var(--white)}

/* brand */
.brand{left:162px;top:34px;display:flex;align-items:center;gap:10px}
.brand-mark{width:22px;height:22px;background:var(--red)}
.brand-name{font-family:"Poppins",sans-serif;font-weight:500;font-size:22px;color:var(--navy);letter-spacing:.3px;white-space:nowrap}

/* nav */
.nav{top:63px;left:579px;font-size:11.5px;color:#8a8a8a;letter-spacing:.2px}
.nav a{color:inherit;text-decoration:none;position:absolute;white-space:nowrap}
.nav a.active{color:var(--ink)}

/* hero */
.hero{left:0;top:105px;width:1200px;height:637px;background:linear-gradient(90deg,#f7f9fc 0%,#eef3f9 30%,#bcd0e6 58%,#7ea4cf 80%,#5b87bd 100%)}
.hero-title{left:162px;top:250px;font-family:"Baloo 2",sans-serif;font-weight:800;font-size:47px;line-height:52px;color:var(--navy);letter-spacing:.5px;white-space:nowrap}
.hero-title .accent{color:var(--red)}
.hero-text{left:162px;top:421px;width:340px;font-size:12.3px;line-height:18.7px;color:#333}
.btn{display:flex;align-items:center;justify-content:center;border-radius:23px;color:var(--white);font-size:13.5px;letter-spacing:.2px}
.hero-btn{left:162px;top:502px;width:128px;height:45px;background:var(--navy)}

/* services */
.services{left:0;top:742px;width:1200px;height:249px;background:var(--soft)}
.service{top:742px;width:202px;text-align:center}
.service-rule{position:absolute;left:0;top:0;width:202px;height:4px;background:var(--red)}
.service-icon{position:absolute;left:71px;top:-28px;width:60px;height:60px;border-radius:50%;background:var(--red);display:flex;align-items:center;justify-content:center}
.service-title{position:absolute;top:51px;left:0;width:202px;font-size:14px;line-height:21px;color:var(--ink)}
.service-text{position:absolute;top:103px;left:0;width:202px;font-size:11.2px;line-height:18.8px;color:var(--muted);font-weight:300}
.service-link{position:absolute;top:172px;left:0;width:202px;font-size:10.5px;color:var(--red);display:flex;justify-content:center;align-items:center;gap:6px}

/* about */
.about-photo{left:162px;top:1050px;width:337px;height:337px;border-radius:50%;background:radial-gradient(circle at 50% 45%,#c8924f 0%,#a57a52 35%,#cfc9c2 65%,#e8e6e3 100%)}
.about-mark{left:579px;top:1052px;width:50px;height:50px;background:var(--red)}
.section-title{font-family:"Baloo 2",sans-serif;font-weight:800;font-size:36px;color:var(--navy);letter-spacing:.5px;white-space:nowrap}
.about-title{left:579px;top:1125px}
.about-text{left:579px;top:1182px;width:462px;font-size:11.6px;line-height:18.8px;color:var(--muted);font-weight:300}
.about-btn{left:577px;top:1343px;width:127px;height:45px;background:var(--red)}

/* contact */
.contact{left:0;top:1446px;width:1200px;height:399px;background:var(--soft)}
.contact-title{left:0;top:1498px;width:1200px;text-align:center}
.contact-sub{left:0;top:1557px;width:1200px;text-align:center;font-size:12.5px;color:#555}
.footer{left:0;top:1845px;width:1200px;height:413px;background:var(--navy)}
.form{left:263px;top:1613px;width:675px;height:307px;background:var(--red)}
.form-frame{position:absolute;inset:15px;border:1px solid rgba(255,255,255,.55)}
.field{position:absolute;background:var(--white);border:1px solid #d9d9d9;font-size:11.5px;color:#666;padding:14px 12px}
.submit{position:absolute;left:277px;top:210px;width:120px;height:44px;border:1.5px solid var(--white);border-radius:22px;color:var(--white);font-size:13px;display:flex;align-items:center;justify-content:center}

/* footer */
.footer-brand{left:0;top:1991px;width:1200px;display:flex;justify-content:center;align-items:center;gap:10px}
.footer-brand .brand-name{color:var(--white)}
.footer-links{left:0;top:2052px;width:1200px;display:flex;justify-content:center;gap:18px;font-size:12px;color:var(--white)}
.footer-links .sep{opacity:.9}
.footer-social{top:2092px;width:38px;height:38px;border-radius:50%;display:flex;align-items:center;justify-content:center}
.footer-social span{width:10px;height:10px;border-radius:50%;background:var(--white)}
.footer-rule{left:161px;top:2191px;width:879px;height:1px;background:rgba(255,255,255,.18)}
.copyright{left:0;top:2219px;width:1200px;text-align:center;font-size:9.8px;color:#b7bacb}
</style>
</head>
<body>

<header>
  <div class="abs topbar"></div>
  <div class="abs topbar-item" style="left:568px">
    <svg width="14" height="14" viewBox="0 0 24 24" fill="#fff"><path d="M6.6 10.8a15.1 15.1 0 0 0 6.6 6.6l2.2-2.2a1 1 0 0 1 1-.25 11.4 11.4 0 0 0 3.6.6 1 1 0 0 1 1 1V20a1 1 0 0 1-1 1A17 17 0 0 1 3 4a1 1 0 0 1 1-1h3.5a1 1 0 0 1 1 1c0 1.25.2 2.45.6 3.6a1 1 0 0 1-.25 1z"/></svg>
    (555) 014 7290
  </div>
  <div class="abs topbar-item" style="left:688px">
    <svg width="16" height="12" viewBox="0 0 16 12" fill="none" stroke="#fff" stroke-width="1.4"><rect x="1" y="1" width="14" height="10"/><path d="M1 1l7 6 7-6"/></svg>
    info@crestlineadvisory.example
  </div>
  <div class="abs topbar-social" style="left:927px"><span></span></div>
  <div class="abs topbar-social" style="left:964px"><span></span></div>
  <div class="abs topbar-social" style="left:1001px;border-right:1px solid rgba(255,255,255,.35)"><span></span></div>

  <div class="abs brand"><div class="brand-mark"></div><div class="brand-name">Crestline Advisory</div></div>

  <nav class="abs nav">
    <a class="active" style="left:0">HOME</a>
    <a style="left:56px">ABOUT COMPANY</a>
    <a style="left:176px">THE TEAM</a>
    <a style="left:250px">WHAT WE DO</a>
    <a style="left:348px">CONTACT US</a>
  </nav>
  <svg class="abs" style="left:1023px;top:63px" width="16" height="16" viewBox="0 0 16 16" fill="none" stroke="#e42528" stroke-width="1.5"><circle cx="7" cy="7" r="5.3"/><path d="M11 11l4 4"/></svg>
</header>

<section>
  <div class="abs hero" role="img" aria-label="Photo of two smiling consultants in blue shirts reviewing charts on a tablet at an office desk"></div>
  <h1 class="abs hero-title">IT AND PROJECT<br><span class="accent">MANAGEMENT<br>CONSULTING</span></h1>
  <p class="abs hero-text">Lorem ipsum dolor sit amet, consectetur adipiscing elit, sed do eiusmod tempor incididunt ut labore et dolore magna aliqua Ut enim ad minim veniam.</p>
  <div class="abs btn hero-btn">LEARN MORE</div>
</section>

<section>
  <div class="abs services"></div>

  <div class="abs service" style="left:161px">
    <div class="service-rule"></div>
    <div class="service-icon"><svg width="32" height="32" viewBox="0 0 32 32" fill="none" stroke="#fff" stroke-width="1.4"><path d="M5 5l4 4M9 5l-4 4M22 23l4 4M26 23l-4 4M14 24l3 3M17 24l-3 3"/><circle cx="7" cy="24" r="2.5"/><path d="M8 20c2-8 10-12 16-10"/><path d="M21 7l3 3-3 3"/></svg></div>
    <div class="service-title">Market<br>Entry</div>
    <div class="service-text">Lorem ipsum dolor sit amet, consectetur  incididunt ulaboris nisi aliquip commodo consequat.</div>
    <div class="service-link">LEARN MORE <svg width="10" height="10" viewBox="0 0 10 10" fill="none" stroke="#e42528" stroke-width="1.3"><path d="M1 9l8-8M3 1h6v6"/></svg></div>
  </div>

  <div class="abs service" style="left:387px">
    <div class="service-rule"></div>
    <div class="service-icon"><svg width="32" height="32" viewBox="0 0 32 32" fill="none" stroke="#fff" stroke-width="1.4"><rect x="7" y="6" width="18" height="22" rx="2"/><rect x="12" y="3" width="8" height="5" rx="1"/><circle cx="16" cy="18" r="5"/><path d="M16 15v3l2 2"/></svg></div>
    <div class="service-title">Technology Ananlysis within<br>healthcare</div>
    <div class="service-text">Lorem ipsum dolor sit amet, consectetur  incididunt ulaboris nisi aliquip commodo consequat.</div>
    <div class="service-link">LEARN MORE <svg width="10" height="10" viewBox="0 0 10 10" fill="none" stroke="#e42528" stroke-width="1.3"><path d="M1 9l8-8M3 1h6v6"/></svg></div>
  </div>

  <div class="abs service" style="left:611px">
    <div class="service-rule"></div>
    <div class="service-icon"><svg width="32" height="32" viewBox="0 0 32 32" fill="none" stroke="#fff" stroke-width="1.4"><path d="M4 16a12 12 0 0 1 24 0c-2-2-4-2-6 0-2-2-4-2-6 0-2-2-4-2-6 0-2-2-4-2-6 0z"/><path d="M16 4v22a3 3 0 0 1-6 0"/></svg></div>
    <div class="service-title">Process Improvement<br>within government</div>
    <div class="service-text">Lorem ipsum dolor sit amet, consectetur  incididunt ulaboris nisi aliquip commodo consequat.</div>
    <div class="service-link">LEARN MORE <svg width="10" height="10" viewBox="0 0 10 10" fill="none" stroke="#e42528" stroke-width="1.3"><path d="M1 9l8-8M3 1h6v6"/></svg></div>
  </div>

  <div class="abs service" style="left:836px">
    <div class="service-rule"></div>
    <div class="service-icon"><svg width="32" height="32" viewBox="0 0 32 32" fill="none" stroke="#fff" stroke-width="1.4"><rect x="4" y="6" width="24" height="16" rx="1"/><path d="M12 27h8M16 22v5M16 9v8M13 14l3 3 3-3"/></svg></div>
    <div class="service-title">Advise for early stage<br>startup</div>
    <div class="service-text">Lorem ipsum dolor sit amet, consectetur  incididunt ulaboris nisi aliquip commodo consequat.</div>
    <div class="service-link">LEARN MORE <svg width="10" height="10" viewBox="0 0 10 10" fill="none" stroke="#e42528" stroke-width="1.3"><path d="M1 9l8-8M3 1h6v6"/></svg></div>
  </div>
</section>

<section>
  <div class="abs about-photo" role="img" aria-label="Circular photo of a smiling consultant in a tan shirt with arms crossed in an office"></div>
  <div class="abs about-mark"></div>
  <h2 class="abs section-title about-title">ABOUT COMPANY</h2>
  <p class="abs about-text">Lorem ipsum dolor sit amet, consectetur adipiscing elit, sed do eiusmod thered tempor incididunt ut labore et dolore magna aliqua. Ut enim ad minim veniam, quis nostrud exercitation ullamco laboris nisi ut aliquip ex ea commodo theryu consequat. Duis aute irure dolor in reprehenderit in voluptate velit esse cillum dolore eu fugiat nulla pariatur. Excepteur sint occaecat cupidatat non proident, sunt in culpa qui officia deserunt mollit anim id est laborum. Lorem ipsum dolor sit amet, consectetur adipiscing elit, sed do eiusmod.</p>
  <div class="abs btn about-btn">LEARN MORE</div>
</section>

<section>
  <div class="abs contact"></div>
  <div class="abs footer"></div>
  <h2 class="abs section-title contact-title">CONTACT US</h2>
  <p class="abs contact-sub">Provide your information below and we'll contact you.</p>
  <form class="abs form">
    <div class="form-frame"></div>
    <div class="field" style="left:53px;top:53px;width:180px;height:44px">Name :</div>
    <div class="field" style="left:247px;top:53px;width:180px;height:44px">Email :</div>
    <div class="field" style="left:443px;top:53px;width:180px;height:44px">Phone :</div>
    <div class="field" style="left:53px;top:113px;width:570px;height:81px;padding-top:10px">Subject :</div>
    <div class="submit">SUBMIT NOW</div>
  </form>
</section>

<footer>
  <div class="abs footer-brand"><div class="brand-mark"></div><div class="brand-name">Crestline Advisory</div></div>
  <div class="abs footer-links">
    <span>Home</span><span class="sep">|</span><span>About Us</span><span class="sep">|</span><span>The Team</span><span class="sep">|</span><span>What We do</span><span class="sep">|</span><span>Contact Us</span>
  </div>
  <div class="abs footer-social" style="left:536px;background:#2fb7ec"><span></span></div>
  <div class="abs footer-social" style="left:581px;background:#4c6bc0"><span></span></div>
  <div class="abs footer-social" style="left:625px;background:#1f8fd1"><span></span></div>
  <div class="abs footer-rule"></div>
  <p class="abs copyright">Copyright © CRESTLINE ADVISORY PTY LTD - 2020 . All Right Reserved.</p>
</footer>

</body>
</html>
```